Stylish Business Cards Wanted

- DOUBLE SIDED Design Required -

High end, edgy cards for a corporate and personal stylist. Must include logo,
Name: Belinda Harwick
Title: Director and Stylist
telephone : +61 8 7142 5809
email: belinda@theloombriefing.example
website: theloombriefing.example
Tag: Corporate Workwear & Uniform Specialist | Personal Stylist
Would like nice icons for telephone, email, website

Target Market(s)

Businesses wanting stylish uniforms, people wanting stylish wardrobes

Industry/Entity Type

Corporate Workwear Stylist

Contact Information for Business Card

I would like black, white and gold foiling incorporated in the design - possibly a touch of the other colours on my branding guide attached Name: Belinda Harwick Title: Director and Stylist telephone : +61 8 7142 5809 email: belinda@theloombriefing.example website: theloombriefing.example Tag: Corporate Workwear & Uniform Specialist | Personal Stylist Would like nice icons for telephone, email, website

Font styles to use
Other font styles liked:
• Raleway

Colors

Designer to choose colors to be used in the design.

Requirements
Must have
• Gold foil accents

```html
<!DOCTYPE html>
<html lang="en">
<head>
<meta charset="utf-8">
<title>The Loom Briefing – Business Card</title>
<link href="https://fonts.googleapis.com/css2?family=Dancing+Script:wght@600&family=Raleway:wght@500;600;700&family=Roboto:wght@400&display=swap" rel="stylesheet">
<style>
  :root {
    --backdrop: #3a3a3c;
    --card: #fbfbfa;
    --navy: #15203a;
    --gold: #e2b653;
    --gold-deep: #c9992f;
    --pink: #e0197a;
    --ink: #1b1b1f;
    --white: #ffffff;
  }
  * { box-sizing: border-box; margin: 0; padding: 0; }
  html, body { width: 799px; height: 1200px; overflow: hidden; }
  body {
    background: var(--backdrop);
    position: relative;
    font-family: "Roboto", sans-serif;
  }
  .card {
    position: absolute;
    left: 80px;
    width: 640px;
    height: 366px;
    background: var(--card);
    border-radius: 26px;
    overflow: hidden;
  }
  .card--front { top: 110px; }
  .card--back { top: 720px; }

  .front-brand {
    position: absolute;
    inset: 0;
    display: flex;
    flex-direction: column;
    align-items: center;
    justify-content: center;
    font-family: "Raleway", sans-serif;
    font-weight: 700;
    color: var(--gold-deep);
    text-align: center;
  }
  .front-brand__name { font-size: 58px; letter-spacing: 2px; line-height: 1.05; }

  .back-art { position: absolute; inset: 0; width: 100%; height: 100%; }

  .contact {
    position: absolute;
    left: 34px;
    top: 34px;
  }
  .contact__name {
    font-family: "Dancing Script", cursive;
    font-weight: 600;
    font-size: 30px;
    color: var(--gold);
    line-height: 1;
  }
  .contact__title { font-size: 12px; color: var(--ink); margin-top: 2px; }
  .contact__list { list-style: none; margin-top: 14px; }
  .contact__item {
    display: flex;
    align-items: center;
    gap: 10px;
    font-size: 14px;
    color: var(--ink);
    height: 22px;
  }
  .contact__icon { width: 13px; height: 13px; flex: none; }
  .contact__dot { width: 11px; height: 11px; border-radius: 50%; background: var(--gold); flex: none; margin: 0 1px; }

  .back-brand {
    position: absolute;
    right: 50px;
    top: 100px;
    font-family: "Raleway", sans-serif;
    font-weight: 700;
    font-size: 36px;
    color: var(--navy);
    letter-spacing: 1px;
    text-align: center;
    line-height: 1.1;
  }

  .services {
    position: absolute;
    right: 34px;
    bottom: 22px;
    list-style: none;
    text-align: right;
    font-family: "Dancing Script", cursive;
    font-weight: 600;
    font-size: 18px;
    color: var(--white);
    line-height: 1.3;
  }
  .services__item::after {
    content: "»";
    color: var(--pink);
    font-family: "Roboto", sans-serif;
    font-size: 14px;
    margin-left: 8px;
  }
</style>
</head>
<body>
  <section class="card card--front">
    <div class="front-brand">
      <span class="front-brand__name">The Loom<br>Briefing</span>
    </div>
  </section>

  <section class="card card--back">
    <svg class="back-art" viewBox="0 0 640 366" preserveAspectRatio="none" aria-hidden="true">
      <path d="M0 0 H22 A22 22 0 0 0 0 60 Z" fill="var(--pink)"/>
      <path d="M0 200 C160 250 330 290 450 250 C530 225 600 215 640 212 V366 H0 Z" fill="var(--navy)"/>
      <path d="M0 186 C160 236 330 276 450 236 C530 211 600 201 640 198" fill="none" stroke="var(--gold)" stroke-width="6"/>
      <path d="M20 218 C150 258 280 288 390 286" fill="none" stroke="var(--gold)" stroke-width="3"/>
    </svg>

    <div class="contact">
      <h1 class="contact__name">Belinda Harwick</h1>
      <p class="contact__title">Director and Stylist</p>
      <ul class="contact__list">
        <li class="contact__item"><span class="contact__dot"></span>/theloombriefing101</li>
        <li class="contact__item">
          <svg class="contact__icon" viewBox="0 0 24 24"><path fill="var(--gold)" d="M6.6 10.8a15.1 15.1 0 0 0 6.6 6.6l2.2-2.2a1 1 0 0 1 1-.25 11.4 11.4 0 0 0 3.6.57 1 1 0 0 1 1 1V20a1 1 0 0 1-1 1A17 17 0 0 1 3 4a1 1 0 0 1 1-1h3.5a1 1 0 0 1 1 1c0 1.25.2 2.45.57 3.57a1 1 0 0 1-.25 1z"/></svg>
          +61 8 7142 5809
        </li>
        <li class="contact__item">
          <svg class="contact__icon" viewBox="0 0 24 24"><rect x="2" y="5" width="20" height="14" rx="2" fill="none" stroke="var(--gold)" stroke-width="2"/><path d="M3 6l9 7 9-7" fill="none" stroke="var(--gold)" stroke-width="2"/></svg>
          belinda@theloombriefing.example
        </li>
        <li class="contact__item">
          <svg class="contact__icon" viewBox="0 0 24 24"><circle cx="12" cy="12" r="10" fill="none" stroke="var(--gold)" stroke-width="2"/><path d="M2 12h20M12 2c3 3 3 17 0 20M12 2c-3 3-3 17 0 20" fill="none" stroke="var(--gold)" stroke-width="2"/></svg>
          theloombriefing.example
        </li>
      </ul>
    </div>

    <div class="back-brand">The Loom<br>Briefing</div>

    <ul class="services">
      <li class="services__item">Personal Stylist</li>
      <li class="services__item">Corporate Workwear</li>
      <li class="services__item">and Uniform Specialist</li>
    </ul>
  </section>
</body>
</html>
```